Create a memorable Web Design for real estate branding

we are a Minnepolis brokerage and boutique housing specialist with over 27 years of experience in the Global furnished housing industry, servicing the Greater Los Angeles area. Specializing in “warm environments” we offer a customized approach to satisfying our guests and client’s needs by offering a wide array of options in highly desirable areas. Additionally, Lantern Dwelling Partners offers assistance and expertise to home buyers, sellers and investors.

Industry/Entity Type

Real Estate

Number of Pages Required

1 page

Font styles to use
Serif
Sans Serif
Decorative

```html
<!DOCTYPE html>
<html lang="en">
<head>
<meta charset="utf-8">
<title>Lantern Dwelling Partners</title>
<link href="https://fonts.googleapis.com/css2?family=Oswald:wght@400;500&family=Open+Sans:wght@400;600;700&display=swap" rel="stylesheet">
<style>
:root{
  --teal:#17a98b;
  --teal-dark:#12937a;
  --green:#7dbb2e;
  --ink:#444;
  --muted:#666;
  --line:#e3e3e3;
  --panel:rgba(45,45,45,.82);
  --footer:#333536;
  --footer-bottom:#2b2c2d;
  --soft:#f2f2f2;
}
*{box-sizing:border-box;margin:0;padding:0}
html,body{width:1200px;height:2497px;overflow:hidden}
body{position:relative;background:#fff;font-family:"Open Sans",sans-serif;color:var(--ink)}
.abs{position:absolute}
a{color:inherit}

/* header */
.brand{left:140px;top:24px;font-family:"Open Sans",sans-serif;font-weight:600;color:var(--teal);font-size:26px;line-height:1.1;display:flex;align-items:center;gap:10px}
.brand-dot{width:16px;height:16px;border-radius:50%;background:var(--teal)}
.social-top{left:790px;top:36px;display:flex;gap:6px}
.social-top span{width:20px;height:20px;border-radius:50%;background:#bfbfbf}
.login{left:906px;top:40px;font-size:12px;font-weight:600;color:#555}
.signup{left:957px;top:30px;width:68px;height:32px;background:var(--green);color:#fff;font-size:12px;font-weight:600;display:flex;align-items:center;justify-content:center;border-radius:2px}

/* nav */
.nav{left:0;top:85px;width:1200px;height:43px;background:var(--teal)}
.nav a{position:absolute;top:14px;font-size:13px;font-weight:700;color:#fff;text-decoration:none;letter-spacing:.3px}

/* hero */
.hero{left:0;top:128px;width:1200px;height:502px;background:linear-gradient(100deg,#5c5a4c 0%,#8a8676 30%,#c8c8bf 60%,#e9eae4 80%,#b9bba8 100%)}
.search-title{left:195px;top:290px;width:803px;height:62px;background:var(--panel);color:#fff;font-family:"Oswald",sans-serif;font-size:29px;text-align:center;line-height:62px;letter-spacing:.3px}
.search-panel{left:195px;top:353px;width:803px;height:172px;background:var(--panel)}
.field{top:32px;height:40px;background:#fff;border-radius:3px;font-size:12px;color:#888;padding-left:16px;line-height:40px}
.field.query{left:30px;width:398px}
.field.category{left:440px;width:185px}
.btn-search{left:637px;top:32px;width:128px;height:40px;background:var(--green);color:#fff;font-size:12px;font-weight:600;display:flex;align-items:center;justify-content:center;gap:12px;border-radius:2px}
.search-only{left:30px;top:96px;color:#fff;font-size:11px;font-weight:700}
.checks{left:30px;top:124px;display:flex;gap:22px;color:#fff;font-size:11px;font-weight:600}
.checks span{display:flex;align-items:center;gap:8px}
.box{width:16px;height:16px;background:#fff;border-radius:3px;display:inline-block;position:relative}
.advanced{left:826px;top:525px;width:172px;height:40px;background:var(--panel);color:var(--teal);font-size:13px;font-weight:600;text-align:center;line-height:40px}

/* section headings */
.section-title{left:0;width:1200px;text-align:center;font-family:"Oswald",sans-serif;font-size:21px;color:#555;font-weight:400}
.section-rule{left:565px;width:70px;height:1px;background:#bbb}

/* cards */
.card{width:224px;background:#fff;box-shadow:0 1px 5px rgba(0,0,0,.13)}
.card .media{height:147px}
.card h3{font-weight:400;color:var(--teal);font-size:18px;margin:14px 20px 8px}
.card p{font-size:12px;color:var(--muted);line-height:1.5;margin:0 20px}
.card .more{display:block;font-size:12px;color:var(--teal);text-decoration:underline;margin:12px 20px 0}

.pager{top:1056px;width:24px;height:24px;border:1px solid #ddd;display:flex;align-items:center;justify-content:center}

/* split band */
.split{left:0;top:1136px;width:1200px;height:314px}
.split h2{position:absolute;font-family:"Oswald",sans-serif;font-weight:400;font-size:22px;color:#fff;top:53px}
.split p{position:absolute;font-size:13.5px;line-height:1.55;color:#fff;top:94px;width:372px}
.pill{top:244px;height:34px;font-size:14px;font-weight:600;display:flex;align-items:center;justify-content:center}
.pill.light{left:345px;width:200px;background:#fff;color:#333;border-radius:17px 0 0 17px}
.pill.teal{left:530px;width:180px;background:var(--teal);color:#fff;border-radius:0 17px 17px 0}

/* testimonial */
.quote-band{left:0;top:1925px;width:1200px;height:212px;background:var(--soft)}
.quote{left:250px;width:700px;text-align:center;font-size:16px;line-height:1.45;color:#444}
.quote-name{left:0;top:2062px;width:1200px;text-align:center;font-size:13px;font-style:italic;color:var(--teal)}

/* footer */
.footer{left:0;top:2137px;width:1200px;height:268px;background:var(--footer);border-top:4px solid var(--teal)}
.footer h4{position:absolute;top:35px;font-family:"Oswald",sans-serif;font-weight:400;color:var(--teal);font-size:13px;letter-spacing:.2px}
.footer .col{position:absolute;top:62px;font-size:11.5px;line-height:18.5px;color:#cfcfcf}
.footer .col .active{color:#fff}
.follow li{list-style:none;display:flex;align-items:center;gap:10px;margin-bottom:14px}
.follow i{width:20px;height:20px;border-radius:50%;background:#e6e6e6;display:inline-block}
.footer-bottom{left:0;top:2405px;width:1200px;height:92px;background:var(--footer-bottom);font-family:"Oswald",sans-serif;font-size:12px;color:#aaa}
</style>
</head>
<body>

<header>
  <div class="abs brand"><span class="brand-dot"></span><span>Lantern Dwelling Partners</span></div>
  <div class="abs social-top"><span></span><span></span><span></span><span></span></div>
  <div class="abs login">LOGIN</div>
  <div class="abs signup">SIGN UP</div>
</header>

<nav class="abs nav">
  <a style="left:140px">HOME</a><a style="left:215px">BUY</a><a style="left:280px">SELL</a>
  <a style="left:345px">VALUATION</a><a style="left:463px">INVESTORS</a><a style="left:571px">SERVICES</a>
  <a style="left:666px">ABOUT</a><a style="left:747px">CAREERS</a><a style="left:842px">CONTACTS</a>
</nav>

<section class="abs hero" role="img" aria-label="Photo of a couple embracing in front of a bright family house"></section>
<div class="abs search-title">SEARCH AND LIST YOUR SWEET HOME FOR SALE</div>
<div class="abs search-panel">
  <div class="abs field query">Search by city, state, country or zip code
    <svg class="abs" style="right:12px;top:11px" width="18" height="18" viewBox="0 0 18 18"><circle cx="7" cy="7" r="5.5" fill="none" stroke="#aaa" stroke-width="2"/><line x1="11" y1="11" x2="16" y2="16" stroke="#aaa" stroke-width="3"/></svg>
  </div>
  <div class="abs field category">All Categories
    <svg class="abs" style="right:12px;top:14px" width="16" height="12"><polygon points="0,0 16,0 8,12" fill="#999"/></svg>
  </div>
  <div class="abs btn-search">SEARCH
    <svg width="18" height="18" viewBox="0 0 18 18"><circle cx="7" cy="7" r="5.5" fill="none" stroke="#fff" stroke-width="2"/><line x1="11" y1="11" x2="16" y2="16" stroke="#fff" stroke-width="3"/></svg>
  </div>
  <div class="abs search-only">SEARCH ONLY:</div>
  <div class="abs checks">
    <span><i class="box"></i>2 BHK</span>
    <span><i class="box"><svg class="abs" style="left:2px;top:2px" width="12" height="12"><polyline points="2,6 5,9 10,2" fill="none" stroke="#7dbb2e" stroke-width="2"/></svg></i>3 BHK</span>
    <span><i class="box"></i>4 BHK</span>
    <span><i class="box"></i>OTHER INPUT TEXT</span>
  </div>
</div>
<div class="abs advanced">ADVANCED SEARCH</div>

<h2 class="abs section-title" style="top:672px">LATEST PROPERTIES</h2>
<div class="abs section-rule" style="top:710px"></div>

<article class="abs card" style="left:107px;top:749px;height:274px"><div class="media" role="img" aria-label="Photo of a white villa with a pool" style="background:linear-gradient(#6fa8dc,#e8e3d4 60%,#2f8fbf)"></div><h3>Birch Lane, NW4</h3><p>4 Bedroom beautifull house for sale for $ 7,15,000....</p><a class="more">Read Details &gt;&gt;</a></article>
<article class="abs card" style="left:360px;top:749px;height:274px"><div class="media" role="img" aria-label="Photo of a living room with white sofas" style="background:linear-gradient(#5a4a3c,#d9d4cc 55%,#7a3b2a)"></div><h3>Birch Lane, NW4</h3><p>4 Bedroom beautifull house for sale for $ 7,15,000....</p><a class="more">Read Details &gt;&gt;</a></article>
<article class="abs card" style="left:615px;top:749px;height:274px"><div class="media" role="img" aria-label="Photo of a modern house with a pool at dusk" style="background:linear-gradient(#1e3f7a,#d5dbe3 55%,#2aa5d8)"></div><h3>Birch Lane, NW4</h3><p>4 Bedroom beautifull house for sale for $ 7,15,000....</p><a class="more">Read Details &gt;&gt;</a></article>
<article class="abs card" style="left:869px;top:749px;height:274px"><div class="media" role="img" aria-label="Photo of a warm lit open plan interior" style="background:linear-gradient(#7b6a58,#c9a77c 50%,#4b3a2c)"></div><h3>Birch Lane, NW4</h3><p>4 Bedroom beautifull house for sale for $ 7,15,000....</p><a class="more">Read Details &gt;&gt;</a></article>

<div class="abs pager" style="left:566px"><svg width="8" height="12"><polyline points="7,1 2,6 7,11" fill="none" stroke="#999" stroke-width="1.5"/></svg></div>
<div class="abs pager" style="left:606px"><svg width="8" height="12"><polyline points="1,1 6,6 1,11" fill="none" stroke="#7dbb2e" stroke-width="1.5"/></svg></div>

<section class="abs split">
  <svg class="abs" style="left:0;top:0" width="1200" height="314" role="img" aria-label="Background photos of a calculator and a hand holding a phone">
    <rect width="1200" height="314" fill="#3a3a3a"/>
    <polygon points="0,0 716,0 498,314 0,314" fill="#17a98b"/>
    <polygon points="716,0 724,0 506,314 498,314" fill="#fff"/>
  </svg>
  <h2 style="left:225px">HOW MUCH IS YOUR HOME WORTH?</h2>
  <p style="left:152px;text-align:right">Lorem ipsum dolor sit amet, consectetur adipisicing elit, sed do eiusmod tempor incididunt ut labore et dolore magna aliqua. Lorem ipsum dolor sit amet, consectetur adipisicing elit, sed do eiusmod tempor incididunt ut labore et dolore magna aliqua.</p>
  <h2 style="left:703px">HAVE ANY QUESTION ON YOUR MIND?</h2>
  <p style="left:703px">Lorem ipsum dolor sit amet, consectetur adipisicing elit, sed do eiusmod tempor incididunt ut labore et dolore magna aliqua. Lorem ipsum dolor sit amet, consectetur adipisicing elit, sed do eiusmod tempor incididunt ut labore et dolore magna aliqua.</p>
  <div class="abs pill light">Request a Valuation</div>
  <div class="abs pill teal">Contact for Query</div>
</section>

<h2 class="abs section-title" style="top:1512px">OUR UNIQUE SERVICES</h2>
<div class="abs section-rule" style="top:1551px"></div>

<article class="abs card" style="left:107px;top:1590px;height:272px"><div class="media" role="img" aria-label="Photo of hands sheltering a small house symbol" style="background:linear-gradient(#1d2b44,#3e5376)"></div><h3>Mortgages</h3><p>Lorem ipsum dolor sit amet, labore et dolore magna aliqua...</p><a class="more">Read More &gt;&gt;</a></article>
<article class="abs card" style="left:360px;top:1590px;height:272px"><div class="media" role="img" aria-label="Photo of paint tins and renovation tools" style="background:linear-gradient(135deg,#e9e4da,#b9a58b 55%,#c43c22)"></div><h3>Refurbishment</h3><p>Lorem ipsum dolor sit amet, labore et dolore magna aliqua...</p><a class="more">Read More &gt;&gt;</a></article>
<article class="abs card" style="left:615px;top:1590px;height:272px"><div class="media" role="img" aria-label="Photo of a mover carrying a cardboard box" style="background:linear-gradient(#e8ecef,#b5946a 60%,#4c4c4c)"></div><h3>Relocation Service</h3><p>Lorem ipsum dolor sit amet, labore et dolore magna aliqua...</p><a class="more">Read More &gt;&gt;</a></article>
<article class="abs card" style="left:869px;top:1590px;height:272px"><div class="media" role="img" aria-label="Photo of a business team standing together" style="background:linear-gradient(#f4f4f4,#9a9aa0 60%,#3b3f48)"></div><h3>Career Training</h3><p>Lorem ipsum dolor sit amet, labore et dolore magna aliqua...</p><a class="more">Read More &gt;&gt;</a></article>

<section class="abs quote-band"></section>
<blockquote class="abs quote" style="top:1971px">"Lorem ipsum dolor sit amet, consectetur adipisicing elit, sed do eiusmod tempor incididunt ut labore et dolore magna aliqua. Ut enim ad minim veniam, quis nostrud exercitation ullamco laboris nisi ut aliquip ex ea commodo consequat."</blockquote>
<div class="abs quote-name">Dana Whitfield, LA</div>
<div class="abs section-rule" style="top:2085px;background:#ccc"></div>

<footer class="abs footer">
  <h4 style="left:107px">QUICK LINKS</h4>
  <div class="col" style="left:107px"><span class="active">Home</span><br>Buy<br>Sell<br>Valuation<br>Services<br>Abou Us<br>Careers<br>Contacts</div>
  <h4 style="left:300px">WARM ENVIRONMENTS</h4>
  <div class="col" style="left:300px;width:205px">Lorem ipsum dolor sit amet, consectetur adipisicing elit, sed do eiusmod tempor incididunt ut labore et dolore magna aliqua. Ut enim ad minim veniam, quis nostrud ullamco ex ea commodo consequat. eiusmod tempor incididunt ut labore et dolore magna aliqua.</div>
  <h4 style="left:614px">OUR OFFICE</h4>
  <div class="col" style="left:614px">480 Orchard Lane, Suite 210<br>Los Angeles, CA 90017<br><br>Phone: +01 555 0142<br>Fax: +01 555 0143<br><br>Email: hello@lanterndwelling.example</div>
  <h4 style="left:879px">FOLLOW US</h4>
  <ul class="col follow" style="left:882px;top:66px"><li><i></i>Neighbors</li><li><i></i>Updates</li><li><i></i>Circles</li><li><i></i>Moodboard</li></ul>
</footer>
<div class="abs footer-bottom">
  <span class="abs" style="left:107px;top:40px">© COPYRIGHT 2016, ALL RIGHT RESERVED</span>
  <span class="abs" style="right:107px;top:40px">TERMS &amp; CONDITIONS &nbsp;|&nbsp; PRIVACY POLICY</span>
</div>

</body>
</html>
```